Chinese restaurant menu and simple logo

We need a menu design for our Chinese fast food restaurant called "Lotus Ladle." We are a small take out Chinese restaurant that has limited seating. Most customers order for take-out. The restaurant has been in business for over 20 years and we need a refresh in our menu as well as logo. This restaurant has always been family run and we have many loyal customers so I would like to keep the feeling of a small business run by a family to serve your family.

For the menu:
We would like to see the colors red, yellow, and whites. I have included a menu mockup we have done but it is lacking design. I have also included pictures of the food we have taken which I would like to see some integrated into the menu. I have also included a reference/sample menu that I think should be the direction we should go in terms of design.

The menu is a trifold so it should be divided into 3 sections with each section being 8.5" x 3.6667" so the total size of the menu unfolded is the standard 8.5" x 11" letter size.

For the logo:
The original logo was just the pagoda picture from the chinese take out boxes sold everywhere with the text "Lotus Ladle" above it. For the redesigned logo, we would like to keep the pagoda theme but maybe just do a silhouette of the pagoda and integrate the restaurant name "Lotus Ladle" into the logo. I have included reference images of pagodas as well. I like the shape of the pagoda from file pagoda_shape.jpg. Which is a more modern silhouette of a pagoda.
Updates

Hi Designers,

I wasn't able to upload all the food photos onto the ArtHivey website so I uploaded it to my filenest: https://www.filenest.example/sh/x4rtplm2kbwqzne/Jt7Vc2LpQr

Target Market(s)

In the area of our restaurant, we serve mostly to individuals from local businesses and city hall employees for lunch and families for dinner. The demographics are mostly African American and Hispanic.

Industry/Entity Type

Fast Food Restaurant

Requirements
Must have
• The menu should be sized 8.5 inches x 11 inches unfolded. It is a tri-fold so when folded up it will be 8.5" x 3.6667".

Please use the text from files:

Pictures:
Please use pictures from my photo food library at the link here: https://www.filenest.example/sh/x4rtplm2kbwqzne/Jt7Vc2LpQr

```html
<!DOCTYPE html>
<html lang="en">
<head>
<meta charset="utf-8">
<title>Lotus Ladle – Logo and Menu</title>
<link href="https://fonts.googleapis.com/css2?family=Kaushan+Script&family=Arimo:wght@400;700&display=swap" rel="stylesheet">
<style>
  :root {
    --paper: #ffffff;
    --backdrop: #efedea;
    --maroon: #5c0f20;
    --maroon-dark: #470a17;
    --gold: #e9b33a;
    --cream: #f6efe4;
    --ink: #111111;
    --script: "Kaushan Script", cursive;
    --sans: "Arimo", Arial, sans-serif;
  }
  * { box-sizing: border-box; margin: 0; padding: 0; }
  html, body { width: 857px; height: 1200px; overflow: hidden; }
  body { background: var(--paper); font-family: var(--sans); }

  .canvas { position: relative; width: 857px; height: 1200px; }

  /* Logo area */
  .logo-area {
    height: 480px; display: flex; flex-direction: column;
    align-items: center; justify-content: center; gap: 26px;
  }
  .logo-mark { width: 150px; height: 150px; border-radius: 50%; background: var(--ink); }
  .logo-name { font-family: var(--script); font-size: 64px; color: var(--ink); line-height: 1; }

  /* Menu area */
  .menu-area {
    position: absolute; top: 480px; left: 0; width: 857px; height: 720px;
    background: var(--backdrop);
    display: flex; justify-content: center; align-items: center;
  }
  .trifold { display: flex; gap: 4px; box-shadow: 0 6px 18px rgba(0,0,0,.18); }
  .panel {
    width: 266px; height: 620px; background: var(--maroon);
    color: var(--cream); padding: 26px 20px; position: relative;
  }

  /* Combination panel */
  .combo-title { font-family: var(--script); color: var(--gold); font-size: 30px; text-align: center; }
  .combo-note { font-size: 13px; color: var(--gold); text-align: center; margin-top: 10px; line-height: 1.5; }
  .combo-deal { font-size: 15px; color: var(--cream); text-align: center; margin-top: 10px; }
  .food-photo {
    background: linear-gradient(135deg, #d98a86 0%, #b84a4a 45%, #5f8a3a 80%, #e9e1d2 100%);
    border: 5px solid #f7f4ee;
  }
  .combo-photo { width: 190px; height: 120px; margin: 24px auto 0; }
  .combo-footer { font-family: var(--script); color: var(--gold); font-size: 22px; text-align: center; margin-top: 40px; }

  /* Cover panel */
  .cover { text-align: center; }
  .cover-mark { width: 86px; height: 86px; border-radius: 50%; background: var(--paper); margin: 30px auto 18px; }
  .cover-name { font-family: var(--script); font-size: 38px; color: var(--paper); line-height: 1; }
  .tagline { font-family: var(--script); color: var(--gold); font-size: 25px; line-height: 1.2; margin-top: 20px; }
  .address { font-size: 12px; line-height: 1.45; margin-top: 26px; }
  .phone { font-size: 23px; color: var(--gold); margin-top: 12px; }
  .hours { font-size: 12px; color: var(--gold); line-height: 1.5; margin-top: 12px; }
  .web { font-size: 12px; color: var(--paper); position: absolute; bottom: 28px; left: 0; right: 0; }

  /* Dishes panel */
  .section-title { font-family: var(--script); color: var(--paper); font-size: 18px; text-align: center; margin: 6px 0 4px; }
  .dish-list { list-style: none; }
  .dish {
    display: flex; font-size: 9.5px; line-height: 1.55; color: var(--cream);
  }
  .dish-name { white-space: nowrap; }
  .dish-dots { flex: 1; border-bottom: 1px dotted rgba(246,239,228,.5); margin: 0 4px 3px; }
  .dish-price { color: var(--gold); }
  .dish-photos { position: relative; height: 150px; margin-top: 8px; }
  .dish-photo-shrimp { position: absolute; right: 0; top: 0; width: 118px; height: 86px;
    background: linear-gradient(135deg, #f2d9bf 0%, #e6b38e 45%, #2f6a2c 85%); border: 5px solid #f7f4ee; }
  .dish-photo-beef { position: absolute; left: 6px; top: 56px; width: 118px; height: 90px; }
  .notes { position: absolute; right: 18px; bottom: 18px; text-align: right; font-size: 9.5px; font-style: italic; color: var(--cream); line-height: 1.5; }
</style>
</head>
<body>
<div class="canvas">

  <header class="logo-area">
    <div class="logo-mark" aria-hidden="true"></div>
    <div class="logo-name">Lotus Ladle</div>
  </header>

  <section class="menu-area">
    <div class="trifold">

      <article class="panel combo">
        <h2 class="combo-title">Combination</h2>
        <p class="combo-note">Choose from Chow Mein,<br>Fried Rice or Steam Rice</p>
        <p class="combo-deal">2 Items for $6.99</p>
        <div class="food-photo combo-photo" role="img" aria-label="Photo of barbecue pork with broccoli"></div>
        <p class="combo-footer">Choose Your Sides</p>
      </article>

      <article class="panel cover">
        <div class="cover-mark" aria-hidden="true"></div>
        <h1 class="cover-name">Lotus Ladle</h1>
        <p class="tagline">The best cantonese<br>food to take home</p>
        <p class="address">518 W. HARBOR BLVD.<br>(corner of Pine &amp; Harbor)<br>in the Village Harbor</p>
        <p class="phone">(555) 014-2288</p>
        <p class="hours">Open 7 Days a Week<br>Monday thru Saturday 11 AM to 9:30 PM<br>Sunday 12:00 PM to 9:30 PM</p>
        <p class="web">http://LotusLadle.example</p>
      </article>

      <article class="panel dishes">
        <h3 class="section-title">chicken</h3>
        <ul class="dish-list">
          <li class="dish"><span class="dish-name">Black Pepper Chicken</span><span class="dish-dots"></span><span class="dish-price">7.99</span></li>
          <li class="dish"><span class="dish-name">Lemon Chicken</span><span class="dish-dots"></span><span class="dish-price">6.99</span></li>
          <li class="dish"><span class="dish-name">Orange Chicken</span><span class="dish-dots"></span><span class="dish-price">6.99</span></li>
          <li class="dish"><span class="dish-name">Kung Pao Chicken *</span><span class="dish-dots"></span><span class="dish-price">6.99</span></li>
          <li class="dish"><span class="dish-name">Chicken Chop Suey</span><span class="dish-dots"></span><span class="dish-price">6.99</span></li>
          <li class="dish"><span class="dish-name">Sesame Chicken</span><span class="dish-dots"></span><span class="dish-price">7.99</span></li>
          <li class="dish"><span class="dish-name">Almond Chicken</span><span class="dish-dots"></span><span class="dish-price">7.99</span></li>
        </ul>
        <h3 class="section-title">beef</h3>
        <ul class="dish-list">
          <li class="dish"><span class="dish-name">Mandarin Beef *</span><span class="dish-dots"></span><span class="dish-price">7.99</span></li>
          <li class="dish"><span class="dish-name">Beef with Oyster Sauce</span><span class="dish-dots"></span><span class="dish-price">7.99</span></li>
          <li class="dish"><span class="dish-name">Black Pepper Beef</span><span class="dish-dots"></span><span class="dish-price">7.99</span></li>
          <li class="dish"><span class="dish-name">Bok Choy Beef</span><span class="dish-dots"></span><span class="dish-price">7.99</span></li>
          <li class="dish"><span class="dish-name">Orange Beef</span><span class="dish-dots"></span><span class="dish-price">8.50</span></li>
        </ul>
        <h3 class="section-title">shrimp</h3>
        <ul class="dish-list">
          <li class="dish"><span class="dish-name">Kung Pao Shrimp *</span><span class="dish-dots"></span><span class="dish-price">7.99</span></li>
          <li class="dish"><span class="dish-name">Shrimp with Lobster Sauce</span><span class="dish-dots"></span><span class="dish-price">7.99</span></li>
          <li class="dish"><span class="dish-name">Shrimp with Black Bean Sauce</span><span class="dish-dots"></span><span class="dish-price">7.99</span></li>
          <li class="dish"><span class="dish-name">Shrimp with Vegetables</span><span class="dish-dots"></span><span class="dish-price">7.99</span></li>
          <li class="dish"><span class="dish-name">Garlic Shrimp</span><span class="dish-dots"></span><span class="dish-price">7.99</span></li>
          <li class="dish"><span class="dish-name">Curry Shrimp *</span><span class="dish-dots"></span><span class="dish-price">7.99</span></li>
          <li class="dish"><span class="dish-name">Sweet &amp; Sour Shrimp</span><span class="dish-dots"></span><span class="dish-price">7.99</span></li>
        </ul>
        <div class="dish-photos">
          <div class="dish-photo-shrimp" role="img" aria-label="Photo of shrimp with broccoli"></div>
          <div class="food-photo dish-photo-beef" role="img" aria-label="Photo of barbecue pork with broccoli"></div>
        </div>
        <p class="notes">* Hot &amp; Spicy<br>Prices subject to change without notice</p>
      </article>

    </div>
  </section>

</div>
</body>
</html>
```